Website for a company offering full serivce charging solutions for electric cars

The company "tanu-werk" (english: "tanu-works") offering all-in-one-solutions for charging infrastructure for electric mobility.

There are four products:
1- Wallboxes for single-family homes
2- Solutions for property devloper/-management for property parking space
3- All-in-one-charging solution for municipalities/communities
4- Solutions for tourism/hotels/holiday appartments

The Website structure:
1. Main Page
2.1. Product Page Single Homes
2.2. Product Page Property Management / Parking
2.3. Product Page Municipality
2.4. Product Page Tourism
3. Contact Form / Request for information
4. Imprint / Legal

The Website should be built on Wordpress with a powerful possibility to simply add/modify specific landing pages.

We would like you to implement the website later and also maintain it if possible, but we would be able to do minor modifications by ourselfs (for A/B-Testing)

The website should be clear and simple, easy to understand.
Target group is mainly B2C without deeper knowledge of that topic.

It should suggest, that we will provide a very simple way to get the charging infrastructure done.

We need a contact form, maybe we will use Hubspot later.

Attached you will find a draft of the main page and a landing page (for 2.2) - it is just the content, please ignore the design. We would love to let you create a suitable design.
Also you will find some drafts a bit different for the same story.

I added also a few stock photos, but they don't need to be used! If you have better ideas, you are welcome!

Industry/Entity Type

Charging/Electric mobility

Number of Pages Required

2 page

Font styles to use
Sans Serif

Requirements
Must have
• Based on Wordpress, and the designer should be able to implement it on Wordpress on a later step

```html
<!DOCTYPE html>
<html lang="de">
<head>
<meta charset="utf-8">
<title>tanu-werk – Ladeinfrastruktur für Elektromobilität</title>
<link rel="stylesheet" href="https://fonts.googleapis.com/css2?family=Exo+2:wght@500;600;700&family=Quicksand:wght@500;600;700&display=swap">
<style>
:root{
  --pink:#e3158d;
  --purple:#8a52d6;
  --white:#ffffff;
  --muted:#d7dbe4;
  --navy:#1b2740;
  --deep:#131a2a;
  --footer:#1a2438;
  --heading:"Exo 2", sans-serif;
  --body:"Quicksand", sans-serif;
}
*{margin:0;padding:0;box-sizing:border-box}
html,body{width:1200px;height:3731px;overflow:hidden}
body{position:relative;background:var(--deep);color:var(--white);font-family:var(--body);font-weight:500}
.abs{position:absolute}
.heading{font-family:var(--heading);font-weight:700;letter-spacing:.5px}
.btn{position:absolute;display:flex;align-items:center;justify-content:center;border-radius:22px;font-family:var(--heading);font-weight:700;font-size:14px;color:var(--white);text-decoration:none;letter-spacing:.3px}
.btn--fill{background:linear-gradient(90deg,var(--pink),var(--purple))}
.btn--line{border:2px solid var(--pink);border-right-color:var(--purple);font-size:12px}

/* hero */
.hero{position:absolute;left:0;top:0;width:1200px;height:558px;background:linear-gradient(100deg,#4d525b 0%,#3a3f47 55%,#2b2f36 100%)}
.hero__visual{position:absolute;left:811px;top:94px;width:389px;height:464px;background:radial-gradient(ellipse at 60% 55%,#e8ecef 0%,#aab3bb 45%,rgba(60,66,74,0) 75%)}
.brand{position:absolute;font-family:var(--heading);font-weight:600;font-size:27px;color:var(--white);letter-spacing:.3px}
.contact-pill{position:absolute;display:flex;align-items:center;gap:10px;font-size:14px;color:var(--white)}
.contact-pill__icon{width:32px;height:32px;border-radius:50%;background:var(--pink);display:flex;align-items:center;justify-content:center}
.contact-pill--phone{background:rgba(255,255,255,.12);border:2px solid var(--purple);border-radius:24px;padding:4px 14px 4px 4px;font-family:var(--heading);font-weight:700;font-size:15px}
.nav{position:absolute;top:66px;left:0;width:1200px;height:30px;font-size:14px}
.nav a{position:absolute;color:var(--white);text-decoration:none;font-weight:600}
.nav .active::after{content:"";position:absolute;left:0;right:0;bottom:-10px;height:3px;border-radius:2px;background:linear-gradient(90deg,var(--pink),var(--purple))}
.hero__kicker{left:163px;top:180px;font-size:33px}
.hero__title{left:163px;top:234px;font-size:38px;line-height:50px;width:560px}

/* partner */
.partner{position:absolute;left:0;top:558px;width:1200px;height:685px;background:var(--navy)}
.photo{position:absolute}
.partner__title{left:604px;top:682px;font-size:34px}
.partner__lead{position:absolute;left:606px;top:741px;width:430px;color:var(--pink);font-weight:700;font-size:16.5px;line-height:24px}
.partner__text{position:absolute;left:606px;top:802px;width:438px;font-size:13px;line-height:24.4px;color:var(--muted)}
.partner__text p{margin-bottom:9px}

/* services */
.services{position:absolute;left:0;top:1243px;width:1200px;height:1930px;background:var(--deep)}
.track{position:absolute;left:0;top:0;width:1200px;height:3731px;pointer-events:none}
.section-title{position:absolute;font-size:34px}
.checks{position:absolute;list-style:none;font-size:13px;line-height:24px;color:var(--muted)}
.checks li{position:relative;padding-left:27px;margin-bottom:8px}
.checks li::before{content:"";position:absolute;left:0;top:5px;width:13px;height:13px;border:1.5px solid var(--pink);border-radius:50%}
.checks li::after{content:"";position:absolute;left:4px;top:8px;width:7px;height:4px;border-left:1.5px solid var(--pink);border-bottom:1.5px solid var(--pink);transform:rotate(-45deg)}
.checks .sub{margin-left:31px}
.round{position:absolute;width:416px;height:416px;border-radius:50%}

/* cta */
.cta{position:absolute;left:0;top:3173px;width:1200px;height:355px;background:linear-gradient(100deg,#3d4967 0%,#2f3a55 100%)}
.cta__visual{position:absolute;left:0;top:0;width:478px;height:355px;background:linear-gradient(90deg,#c9ced3 0%,#9da4ac 45%,rgba(61,73,103,0) 100%)}
.cta__title{left:567px;top:3270px;width:460px;font-size:35px;line-height:41px}

/* footer */
.footer{position:absolute;left:0;top:3528px;width:1200px;height:203px;background:var(--footer)}
.footer__links a{position:absolute;top:3597px;font-size:12px;font-weight:600;color:var(--white);text-decoration:none}
.copy{position:absolute;left:163px;top:3700px;font-size:11px;color:var(--white)}
.social{position:absolute;top:3691px;width:32px;height:32px;border-radius:50%;border:1.5px solid var(--white)}
</style>
</head>
<body>

<header class="hero">
  <div class="hero__visual" role="img" aria-label="Drei weiße Ladesäulen mit angeschlossenen weißen Elektroautos"></div>
</header>
<div class="brand" style="left:160px;top:58px">tanu-werk.de</div>
<div class="contact-pill" style="left:605px;top:15px">
  <span class="contact-pill__icon"><svg width="16" height="12" viewBox="0 0 16 12"><rect x="0.5" y="0.5" width="15" height="11" rx="1.5" fill="#fff"/><path d="M1 1.5 8 7l7-5.5" stroke="#e3158d" stroke-width="1.5" fill="none"/></svg></span>
  info@tanu-werk.de
</div>
<div class="contact-pill contact-pill--phone" style="left:822px;top:12px">
  <span class="contact-pill__icon" style="background:#fff"><svg width="16" height="16" viewBox="0 0 24 24"><path d="M6.6 10.8a15 15 0 0 0 6.6 6.6l2.2-2.2c.3-.3.7-.4 1-.2 1.1.4 2.3.6 3.6.6.6 0 1 .4 1 1V20c0 .6-.4 1-1 1A17 17 0 0 1 3 4c0-.6.4-1 1-1h3.5c.6 0 1 .4 1 1 0 1.3.2 2.5.6 3.6.1.3 0 .7-.2 1z" fill="#e3158d"/></svg></span>
  123 555 0190 (Zollfrei)
</div>
<nav class="nav">
  <a class="active" style="left:514px">Lösungen</a>
  <a style="left:615px">Unternehmen</a>
  <a style="left:744px">Dienstleistungen</a>
  <a style="left:892px">Karriere</a>
  <a style="left:984px">Kontakt</a>
</nav>
<div class="abs heading hero__kicker">tanu-werk</div>
<h1 class="abs heading hero__title">All-in-One-Lösungen Für Ladeinfrastruktur Für Elektromobilität Anzubieten.</h1>
<a class="btn btn--fill" style="left:161px;top:413px;width:218px;height:40px">Kontaktiere Uns Heute</a>

<section class="partner"></section>
<div class="photo" role="img" aria-label="Frau mit Smartphone neben einem ladenden Elektroauto bei Sonnenuntergang" style="left:246px;top:690px;width:227px;height:227px;border-radius:22px 22px 22px 70px;background:linear-gradient(135deg,#e0a552,#6b4a33 60%,#cfd2d5)"></div>
<div class="photo" role="img" aria-label="Ladestecker mit blau leuchtendem Ring" style="left:162px;top:848px;width:190px;height:217px;border-radius:18px 70px 18px 18px;background:linear-gradient(135deg,#e9edf2,#9fb0c6 55%,#3a6fd8)"></div>
<div class="photo" role="img" aria-label="Hand steckt Ladekabel in ein Elektroauto" style="left:358px;top:924px;width:227px;height:228px;border-radius:70px 22px 22px 22px;background:linear-gradient(135deg,#5f8fc4,#b6c9dc 50%,#2b3b52)"></div>
<h2 class="abs heading partner__title">tanu-werk ist Ihr Partner</h2>
<p class="partner__lead">wenn das Laden nicht nur einfach, sondern die Umsetzung auch aus einer Hand kommen soll</p>
<div class="partner__text">
  <p>Wir bieten Lösungen sowohl für Privatkunden, Geschäftskunden als auch Kommunen an, die schnell, fair und ohne Eigenleistung zu einer smarten Ladelösung für E-Fahrzeuge kommen möchten.</p>
  <p>Von der Beratung, über die Installation, Inbetriebnahme bis zur Abrechnung und Wartung bekommen Sie bei tanu-werk alles aus einer Hand. Auf Wunsch vermieten wir auch die Ladetechnik und übernehmen im gewerblichen Bereich die direkte Abrechnung mit dem Nutzer. Für Kommunen bieten wir den kostenfreien Full-Service an und beteiligen die Gemeinden an der Nutzung der Infrastruktur.</p>
  <p>Fragen Sie uns nach der auf Ihre individuellen Bedürfnisse zugeschnittenen Lösung:</p>
</div>
<a class="btn btn--line" style="left:606px;top:1124px;width:204px;height:36px">Kontaktieren Sie uns heute</a>

<section class="services"></section>

<div class="round" role="img" aria-label="Lächelnde Frau steckt Ladekabel in ein rotes Elektroauto" style="left:633px;top:1322px;background:linear-gradient(135deg,#3a2b26,#8a5a3a 40%,#d22b2b 80%)"></div>
<div class="round" role="img" aria-label="Weiße Wallbox mit Ladestecker an einem silbernen Auto" style="left:153px;top:1768px;background:linear-gradient(135deg,#e6e2d8,#b7b3a7 45%,#5b5a55)"></div>
<div class="round" role="img" aria-label="Transparente Fahrzeugdarstellung zwischen zwei Ladesäulen" style="left:633px;top:2214px;background:linear-gradient(135deg,#8fa2b6,#c9d2da 50%,#6d7a86)"></div>
<div class="round" role="img" aria-label="Blaues Auto mit orangem Ladekabel an einer Ladesäule" style="left:153px;top:2660px;background:linear-gradient(135deg,#2a4f8f,#3f6cb5 50%,#e27a2a 85%)"></div>

<svg class="track" viewBox="0 0 1200 3731" aria-hidden="true">
  <defs>
    <linearGradient id="track-grad" x1="130" y1="0" x2="1080" y2="0" gradientUnits="userSpaceOnUse">
      <stop offset="0" stop-color="#e3158d"/>
      <stop offset="1" stop-color="#8a52d6"/>
    </linearGradient>
  </defs>
  <path d="M841 1307 A223 223 0 0 1 841 1753 L361 1753 A223 223 0 0 0 361 2199 L841 2199 A223 223 0 0 1 841 2645 L361 2645 A223 223 0 0 0 361 3091 L1080 3091 Q1098 3091 1098 3073 L1098 3000" fill="none" stroke="url(#track-grad)" stroke-width="6" stroke-linecap="round"/>
</svg>

<h2 class="heading section-title" style="left:164px;top:1332px">als Privatkunde</h2>
<ul class="checks" style="left:170px;top:1400px;width:395px">
  <li>Bestandsanalyse mit umfangreicher Beratung über die Möglichkeiten der Umsetzung</li>
  <li>Prüfung und Übernahme der Anmeldung verfügbarer Fördermöglichkeiten</li>
  <li>Auswahl an smarten Wallbox Lösungen, passend für Ihr Fahrzeug und Ihre Bedürfnisse</li>
  <li>Installation inkl. aller notwendigen Materialien und Tätigkeiten (Durchbrüche, Erdarbeiten, etc.)</li>
  <li>Inbetriebnahme und Einweisung in die Ladetechnik</li>
  <li>Jährlich technische Wartung nach DGUV3</li>
  <li>Reparaturservice, unter Berücksichtigung der geltenden Garantie Ansprüche</li>
</ul>

<h2 class="heading section-title" style="left:596px;top:1790px">als Geschäftskunde</h2>
<ul class="checks" style="left:596px;top:1850px;width:430px">
  <li>Durchführung einer individuellen Bedarfsanalyse inkl. Ermittlung der Anforderungen für:</li>
  <li class="sub">Haus- und Immobilienverwaltungen</li>
  <li class="sub">Dienstleistungs- und Handelsunternehmen</li>
  <li class="sub">Hotel und Beherbergungsbetriebe</li>
  <li class="sub">Parkraum- und Parkhausbetreiber</li>
  <li class="sub">Tourismus, Sport- und Freizeiteinrichtungen</li>
  <li>Planung und Projektierung des Installationsaufwands inkl. Materialverbrauch</li>
  <li>Leasing oder Kauf der Hardware</li>
</ul>

<ul class="checks" style="left:161px;top:2248px;width:430px">
  <li>Normgerechte Installation der Ladeinfrastruktur inkl. Durchbruch-, Brandschutz- und Erdarbeiten</li>
  <li>Leasing oder Kauf der Hardware</li>
  <li>Bei Bestandsbauten Integration der Ladeinfrastruktur in die Gebäudesystemtechnik und ggf. Anpassung des Netzanschlusses</li>
  <li>Inbetriebnahme der Anlage inkl. Prüf- und Messprotokollen</li>
  <li>Wiederkehrende technische Prüfung der Anlage nach DGUV 3</li>
  <li>Austausch und Reparatur Service</li>
  <li>Unterstützung bei der mtl. Nutzungsabrechnung und Einbindung in Ihre vorhandene Abrechnungssysteme</li>
  <li>ODER direkte Abrechnung mit den Nutzern</li>
</ul>

<h2 class="heading section-title" style="left:625px;top:2664px">als Kommune</h2>
<ul class="checks" style="left:626px;top:2722px;width:420px">
  <li>Konzeptionierung möglicher Ladeinfrastrukturen innerhalb Ihrer Gemeinde</li>
  <li>Planung und Projektsteuerung inkl. sämtlicher behördlicher Genehmigungsverfahren und Beantragung von Fördermitteln</li>
  <li>Fachgerechte Installation und Inbetriebnahme</li>
  <li>Regelmäßige Wartung gemäß Vorschrif</li>
  <li>Reparatur und Kundenservice</li>
  <li>Direkte Abrechnung mit dem Nutzer</li>
  <li>Beteiligung der Gemeinde am Umsatz</li>
  <li>Möglichkeit der Integration von Bonusprogrammen, mit denen der lokale Einzelhandel beworben wird</li>
</ul>

<section class="cta">
  <div class="cta__visual" role="img" aria-label="Weißes Elektroauto an einer freistehenden Ladesäule"></div>
</section>
<h2 class="abs heading cta__title">Werden Sie unser Partner oder Gastgeber der Ladestation</h2>
<a class="btn btn--fill" style="left:567px;top:3400px;width:243px;height:39px">Kontaktieren Sie uns heute</a>

<footer class="footer"></footer>
<div class="brand" style="left:160px;top:3612px">tanu-werk.de</div>
<nav class="footer__links">
  <a style="left:396px">AGB</a>
  <a style="left:464px">Datenschutzerklärung</a>
  <a style="left:636px">Impressum</a>
  <a style="left:740px">Kontakt</a>
  <a style="left:829px">Karriere</a>
  <a style="left:917px">Kontakt</a>
  <a style="left:1003px">FAQs</a>
</nav>
<div class="copy">©tanu-werk GmbH</div>
<span class="social" style="left:910px"></span>
<span class="social" style="left:958px"></span>
<span class="social" style="left:1006px"></span>

</body>
</html>
```